Fahrzeugaufbereitung inkl. Hol- und Bringedienst
Zielgruppe
Für Privatkunden
Aufgabenstellung
Benötige einen Flyer, um Privatkunden unseren neuen Hol- und Bringedienst für Fahrzeugaufbereitung vorzustellen.
Text und Preise unter www.belvo-fahrdienst.de unter Fahrzeugaufbereitung.
Format Din Lang (105x210mm), zweiseitig

```html
<!DOCTYPE html>
<html lang="de">
<head>
<meta charset="utf-8">
<title>BELVO Fleetservices – Flyer DIN lang</title>
<link rel="stylesheet" href="https://fonts.googleapis.com/css2?family=Fjalla+One&family=Roboto+Condensed:wght@400;700&display=swap">
<style>
  :root {
    --brand-blue: #2a9fd8;
    --ink: #111214;
    --paper: #ffffff;
    --stage: #e9e6e1;
    --muted: #9a9a9a;
    --line: #d6d6d6;
  }
  * { box-sizing: border-box; margin: 0; padding: 0; }
  html, body { width: 1200px; height: 1200px; overflow: hidden; }
  body {
    background: var(--stage);
    font-family: "Roboto Condensed", "Arial Narrow", sans-serif;
    color: var(--ink);
    position: relative;
  }
  .flyer {
    position: absolute;
    left: 100px;
    width: 1000px;
    height: 500px;
    background: var(--ink);
    box-shadow: 0 10px 30px rgba(0,0,0,.18);
    overflow: hidden;
  }
  .flyer--front { top: 80px; }
  .flyer--back { top: 620px; }

  /* header band */
  .flyer__head {
    background: var(--paper);
    height: 180px;
    display: flex;
    align-items: center;
    padding: 0 46px;
  }
  .brand {
    font-family: "Fjalla One", sans-serif;
    color: var(--brand-blue);
    display: flex;
    align-items: center;
    gap: 14px;
    width: 250px;
  }
  .brand__dot {
    width: 18px; height: 18px; border-radius: 50%;
    background: var(--brand-blue);
    flex: none;
  }
  .brand__name {
    font-size: 40px;
    line-height: 1;
    letter-spacing: 1px;
  }
  .brand__name small {
    display: block;
    font-size: 17px;
    letter-spacing: 2px;
    margin-top: 4px;
  }
  .divider {
    width: 2px; height: 96px;
    background: var(--line);
    margin: 0 40px 0 20px;
  }
  .offer__title {
    font-family: "Fjalla One", sans-serif;
    font-size: 38px;
    line-height: 1.1;
  }
  .offer__sub {
    font-family: "Fjalla One", sans-serif;
    font-size: 24px;
    color: #333;
    margin-top: 4px;
  }
  .price {
    margin-left: auto;
    font-family: "Fjalla One", sans-serif;
    color: var(--brand-blue);
    display: flex;
    align-items: flex-end;
    gap: 10px;
  }
  .price__lead { font-size: 30px; padding-bottom: 14px; }
  .price__amount { font-size: 104px; line-height: .9; }
  .price__cents { font-size: 40px; align-self: flex-start; margin-left: -6px; }

  /* front: steps */
  .steps { padding: 28px 46px 0; }
  .steps__title {
    font-family: "Fjalla One", sans-serif;
    color: var(--brand-blue);
    font-size: 30px;
  }
  .steps__row {
    display: flex;
    align-items: center;
    justify-content: space-between;
    margin-top: 24px;
  }
  .step {
    width: 196px; height: 196px;
    border: 2px solid var(--paper);
    border-radius: 50%;
    display: flex; align-items: center; justify-content: center;
  }
  .step__art {
    width: 130px; height: 110px;
    border-radius: 18px;
    background: radial-gradient(circle at 50% 55%, #f2f2f2 0%, #bfc6cc 55%, #2a9fd8 100%);
    opacity: .85;
  }
  .step__arrow { width: 34px; height: 34px; }

  /* back */
  .contact {
    display: flex;
    gap: 40px;
    margin-left: 30px;
    font-size: 18px;
    line-height: 1.55;
    color: #222;
  }
  .contact__title {
    font-family: "Fjalla One", sans-serif;
    color: var(--brand-blue);
    font-size: 28px;
    margin-bottom: 4px;
  }
  .contact__col--right { padding-top: 40px; }
  .info {
    display: flex;
    gap: 50px;
    padding: 34px 46px 0;
    color: var(--paper);
  }
  .info__col { flex: 1; }
  .info__title {
    font-family: "Fjalla One", sans-serif;
    color: var(--brand-blue);
    font-size: 28px;
    margin-bottom: 12px;
  }
  .info__text { font-size: 18px; line-height: 1.5; }
  .info__note { font-size: 13px; color: var(--muted); margin-top: 12px; }
  .services { list-style: none; font-size: 18px; line-height: 1.6; }
  .services li::before { content: "• "; }
</style>
</head>
<body>

<section class="flyer flyer--front" aria-label="Flyer Vorderseite">
  <header class="flyer__head">
    <div class="brand">
      <span class="brand__dot"></span>
      <span class="brand__name">BELVO<small>FLEETSERVICES GmbH</small></span>
    </div>
    <div class="divider"></div>
    <div class="offer">
      <h1 class="offer__title">Fahrzeugaufbereitung</h1>
      <p class="offer__sub">inkl. Hol- und Bringedienst</p>
    </div>
    <div class="price">
      <span class="price__lead">nur €</span>
      <span class="price__amount">59,</span>
      <span class="price__cents">90*</span>
    </div>
  </header>

  <div class="steps">
    <h2 class="steps__title">Und so funktioniert's:</h2>
    <div class="steps__row">
      <div class="step">
        <svg width="110" height="120" viewBox="0 0 110 120" aria-label="Telefon">
          <path d="M62 22a18 18 0 0 1 22 0M56 12a30 30 0 0 1 34 0" fill="none" stroke="var(--brand-blue)" stroke-width="5" stroke-linecap="round"/>
          <rect x="33" y="30" width="42" height="78" rx="7" fill="var(--paper)"/>
          <rect x="40" y="38" width="28" height="22" rx="2" fill="var(--ink)"/>
          <g fill="var(--ink)">
            <rect x="40" y="68" width="7" height="6"/><rect x="50.5" y="68" width="7" height="6"/><rect x="61" y="68" width="7" height="6"/>
            <rect x="40" y="78" width="7" height="6"/><rect x="50.5" y="78" width="7" height="6"/><rect x="61" y="78" width="7" height="6"/>
            <rect x="40" y="88" width="7" height="6"/><rect x="50.5" y="88" width="7" height="6"/><rect x="61" y="88" width="7" height="6"/>
          </g>
        </svg>
      </div>
      <svg class="step__arrow" viewBox="0 0 34 34" aria-hidden="true"><path d="M2 11h16V3l14 14-14 14v-8H2z" fill="var(--paper)"/></svg>
      <div class="step"><div class="step__art" role="img" aria-label="Illustration: Fahrzeug wird zu Hause abgeholt"></div></div>
      <svg class="step__arrow" viewBox="0 0 34 34" aria-hidden="true"><path d="M2 11h16V3l14 14-14 14v-8H2z" fill="var(--paper)"/></svg>
      <div class="step"><div class="step__art" role="img" aria-label="Illustration: Fahrzeug wird gereinigt und geprüft"></div></div>
      <svg class="step__arrow" viewBox="0 0 34 34" aria-hidden="true"><path d="M2 11h16V3l14 14-14 14v-8H2z" fill="var(--paper)"/></svg>
      <div class="step"><div class="step__art" role="img" aria-label="Illustration: sauberes Fahrzeug wird zurückgebracht"></div></div>
    </div>
  </div>
</section>

<section class="flyer flyer--back" aria-label="Flyer Rückseite">
  <header class="flyer__head">
    <div class="brand">
      <span class="brand__dot"></span>
      <span class="brand__name">BELVO<small>FLEETSERVICES GmbH</small></span>
    </div>
    <div class="contact">
      <div class="contact__col">
        <h2 class="contact__title">Kontakt</h2>
        <p>B.E.L.V.O GmbH<br>Lindenhofstr. 42<br>10827 Berlin</p>
      </div>
      <div class="contact__col contact__col--right">
        <p>Tel. 030 41 57 26 3 -0<br>Mail info@belvo-fahrdienst.de<br>Web www.belvo-fahrdienst.de</p>
      </div>
    </div>
  </header>

  <div class="info">
    <div class="info__col">
      <h2 class="info__title">Unser Service für Sie</h2>
      <p class="info__text">Wir bieten Ihnen eine klassische <strong>Fahrzeugaufbereitung inkl. Hol- und Bringedienst</strong> für nur <strong>€ 59,90*</strong> an. Sparen Sie Ihre wertvolle Zeit und lassen Sie Ihr Fahrzeug von uns an Ihrem Wunschort abholen und innerhalb der nächsten <strong>90 Minuten</strong> aufbereiten.</p>
      <p class="info__note">*Preis inkl. MwSt. und freibleibend.</p>
    </div>
    <div class="info__col">
      <h2 class="info__title">Unser Leistungsangebot enthält</h2>
      <ul class="services">
        <li>Hol- und Bringeservice</li>
        <li>Aussenwäsche inkl. Felgenreinigung</li>
        <li>Innenreinigung inkl. Cockpit und Saugen</li>
        <li>Fensterreinigung innen &amp; aussen</li>
        <li>Öl-, Wasser- und Wischwasserkontrolle</li>
        <li>Reifendruck und Profilkontrolle</li>
      </ul>
    </div>
  </div>
</section>

</body>
</html>
```